velorahelp Web Design Project

It is a virtual assistance/concierge company that helps the busy professional by remotely providing administrative, technical and/or creative business support services, specializing in the medical device industry. Company name is velorahelp.
(website will be velorahelp.example)

Allowing things to be done without taking time away from more urgent issues or family/personal time. Partnering with a VA reduces stress, protects cash flow, eliminates administrative hassles, and enables business people to find the success they originally set out to achieve. Saves small businesses and/or individuals on overhead, salary, et. Work is done remotely to offer administrative, clerical, typing and specialist service assistance on a regular, ad-hoc or emergency cover basis.

Though we are capable of addressing the needs of medical professionals and industry representatives due to our experience and knowledge (sales, HCC guidelines, etc.) we do not want to be limited to that market only.

Target Market(s)

Target market would be M/F, 30-50, National, busy, Alpha, entrepreneurs and industry professionals who want/need to do more without sacrifice of life

Requirements
Nice to have
• We do have a logo designed via the PlanMarket website that can/should be included. Logo is uploaded.

```html
<!DOCTYPE html>
<html lang="en">
<head>
<meta charset="utf-8">
<title>velorahelp</title>
<link rel="stylesheet" href="https://fonts.googleapis.com/css2?family=Signika:wght@400;600&family=Arimo:wght@400;700&display=swap">
<style>
:root{
  --navy:#1f3f66;
  --navy-dark:#163253;
  --red:#c8190f;
  --red-dark:#a51208;
  --ink:#1a1a1a;
  --text:#333;
  --muted:#777;
  --panel:#555;
  --panel-btn:#b5b5b5;
  --band:#ebebeb;
  --quote-bg:#e6e6e6;
  --footer:#9a9a9a;
  --white:#fff;
}
*{box-sizing:border-box;margin:0;padding:0}
html,body{width:1052px;height:1200px;overflow:hidden;background:var(--white)}
body{font-family:"Arimo",Arial,sans-serif;color:var(--text);position:relative}

.site-header{position:absolute;left:0;top:0;width:1052px;height:86px}
.brand{position:absolute;left:78px;top:20px;display:flex;align-items:center;gap:8px;font-family:"Signika",sans-serif;font-weight:600;font-size:40px;color:var(--navy);line-height:1}
.brand-dot{width:18px;height:18px;border-radius:50%;background:var(--red)}
.phone{position:absolute;left:630px;top:42px;font-size:11.5px;color:var(--muted);display:flex;align-items:center;gap:6px}
.search{position:absolute;left:798px;top:35px;width:178px;height:26px;display:flex}
.search-field{flex:1;border:1px solid #bdbdbd;border-right:none;border-radius:3px 0 0 3px;font-size:11.5px;color:#888;padding:6px 8px;background:#fff}
.search-btn{width:30px;background:#8f8f8f;border-radius:0 3px 3px 0;display:flex;align-items:center;justify-content:center}

.main-nav{position:absolute;left:0;top:86px;width:1052px;height:52px;background:linear-gradient(var(--navy),var(--navy-dark))}
.main-nav a{position:absolute;top:0;height:52px;line-height:52px;text-align:center;color:var(--white);text-decoration:none;font-family:"Signika",sans-serif;font-size:16px}
.main-nav a.active{background:linear-gradient(#d82a1c,#b51309)}
.nav-sep{position:absolute;top:8px;width:1px;height:36px;background:rgba(255,255,255,.25)}

.slider-text{position:absolute;left:78px;top:150px;width:257px;height:305px;background:var(--panel);color:#bdbdbd}
.slider-text h2{position:absolute;left:14px;top:62px;color:var(--white);font-family:"Signika",sans-serif;font-weight:400;font-size:20px}
.slider-text p{position:absolute;left:14px;top:98px;width:232px;font-size:11px;line-height:17.5px}
.arrow-btn{position:absolute;right:0;width:53px;height:26px;background:var(--panel-btn);display:flex;align-items:center;justify-content:center}
.slider-photo{position:absolute;left:350px;top:150px;width:626px;height:305px;border:1px solid #ddd;background:linear-gradient(90deg,#f4f4f4,#e8e1da 40%,#b9b9c2 75%,#eef1f6)}

.slider-bar{position:absolute;left:78px;top:455px;width:898px;height:51px;background:#f2f2f2;border-top:3px solid var(--red);border-radius:0 0 6px 6px;box-shadow:0 3px 6px rgba(0,0,0,.35)}
.slider-bar .bar-title{position:absolute;left:19px;top:14px;font-size:16px;color:var(--ink)}
.slider-bar .bar-divider{position:absolute;left:132px;top:10px;width:1px;height:32px;background:#bbb}
.slider-bar .bar-text{position:absolute;left:158px;top:17px;font-size:12.5px;color:#444}
.btn-read{position:absolute;right:12px;top:10px;width:88px;height:28px;background:var(--red);border-radius:4px;color:var(--white);font-family:"Signika",sans-serif;font-size:12.5px;text-align:center;line-height:28px}

.welcome{position:absolute;left:79px;top:532px;width:607px}
.section-title{font-family:"Signika",sans-serif;font-weight:400;font-size:22px;color:var(--ink)}
.welcome p{font-size:11.1px;line-height:16.6px;text-align:justify;margin-top:24px}
.welcome p + p{margin-top:33px}

.testimonials{position:absolute;left:704px;top:532px;width:272px}
.testi-nav{position:absolute;right:0;top:0;display:flex;gap:4px}
.testi-nav span{width:17px;height:17px;border:1px solid #ccc;border-radius:3px;background:#f6f6f6;display:flex;align-items:center;justify-content:center}
.quote-box{position:absolute;left:3px;top:36px;width:267px;height:183px;background:var(--quote-bg);padding:18px 7px 0 18px}
.quote-mark{position:absolute;left:18px;top:16px}
.quote-head{margin-left:42px;font-family:"Signika",sans-serif;font-size:15px;color:var(--red)}
.quote-sub{margin-left:42px;font-size:11px;color:#444;margin-top:1px}
.quote-box p{font-size:10.8px;line-height:16.6px;text-align:justify;margin-top:14px}

.projects{position:absolute;left:0;top:783px;width:1052px;height:349px;background:var(--band)}
.projects .section-title{position:absolute;left:79px;top:29px}
.card{position:absolute;top:79px;width:265px;height:255px;background:var(--white)}
.card-photo{height:137px;background:linear-gradient(90deg,#3a3530,#c9b3a0 45%,#e3e3e3)}
.card-title{height:31px;background:linear-gradient(#e21d0c,#b81208);color:var(--white);font-family:"Signika",sans-serif;font-size:16px;padding:5px 0 0 19px;margin-left:-2px}
.card p{font-size:10.8px;line-height:16.6px;padding:14px 20px 0;text-align:justify}

.site-footer{position:absolute;left:0;top:1155px;width:1052px;height:45px;background:var(--footer);color:var(--white);font-size:8.5px;padding:17px 0 0 78px}
</style>
</head>
<body>

<header class="site-header">
  <div class="brand"><span class="brand-dot"></span>velorahelp</div>
  <div class="phone">
    <svg width="8" height="13" viewBox="0 0 8 13"><path d="M6 1 C2 2 1 6 2 10 L4 12 L6 10 L4 8 C3 6 4 4 6 3 Z" fill="#999"/></svg>
    Phone number comes here
  </div>
  <div class="search">
    <div class="search-field">Search</div>
    <div class="search-btn"><svg width="16" height="16" viewBox="0 0 16 16"><circle cx="6.5" cy="6.5" r="4.5" fill="none" stroke="#fff" stroke-width="1.8"/><path d="M10 10 L14 14" stroke="#fff" stroke-width="2.4"/></svg></div>
  </div>
</header>

<nav class="main-nav">
  <a class="active" style="left:78px;width:120px">HOME</a>
  <a style="left:198px;width:185px">ABOUT US</a>
  <span class="nav-sep" style="left:383px"></span>
  <a style="left:383px;width:175px">SERVICES</a>
  <span class="nav-sep" style="left:558px"></span>
  <a style="left:558px;width:258px">TECHNICAL SUPPORT</a>
  <span class="nav-sep" style="left:816px"></span>
  <a style="left:816px;width:160px">CONTACT US</a>
</nav>

<section class="slider-text">
  <span class="arrow-btn" style="top:0"><svg width="14" height="8" viewBox="0 0 14 8"><path d="M1 7 L7 1 L13 7" fill="none" stroke="#555" stroke-width="1.6"/></svg></span>
  <h2>Lorem Ipsum</h2>
  <p>It dummy text of the printing and typesetting industry. Lorem Ipsum has been the industry's standard dummy text ever since the 1500s, when an unknown printer took a galley of type and scrambled it to make a type specimen book.Lorem Ipsum is simply dummy text of the printing and typesetting industry. make a type specimen book.</p>
  <span class="arrow-btn" style="bottom:0"><svg width="14" height="8" viewBox="0 0 14 8"><path d="M1 1 L7 7 L13 1" fill="none" stroke="#555" stroke-width="1.6"/></svg></span>
</section>
<div class="slider-photo" role="img" aria-label="Photo of a smiling team of five business professionals"></div>

<div class="slider-bar">
  <span class="bar-title">Lorem Ipsum</span>
  <span class="bar-divider"></span>
  <span class="bar-text">Lorem Ipsum is simply dummy text of the printing and typesetting industry.</span>
  <span class="btn-read">READ MORE</span>
</div>

<section class="welcome">
  <h2 class="section-title">Hello and Welcome</h2>
  <p>Lorem Ipsum is simply dummy text of the printing and typesetting industry. Lorem Ipsum has been the industry's stdard dummy text ever since the 1500s, when an unknown printer took a galley of type and scrambled it to make a type spemen book. It has survived not only five centuries, but also the leap into electronic typesetting, remaining essetially unchanged.</p>
  <p>It was popularised in the 1960s with the release of Kelvane sheets containing Lorem Ipsum pasages, and more recently with desktop publishing software like Pressline Studio including versions of Lorem Ipsum. Ipsum pasages, and more recently with desktop publishing software like Pressline Studio including versions of Lorem Ipsum.pasages, and more recently with desktop publishing software like Pressline Studio including versions of Lorem Ipsum.</p>
</section>

<aside class="testimonials">
  <h2 class="section-title">Testimonials</h2>
  <div class="testi-nav">
    <span><svg width="6" height="9" viewBox="0 0 6 9"><path d="M5 1 L1 4.5 L5 8" fill="none" stroke="#555" stroke-width="1.5"/></svg></span>
    <span><svg width="6" height="9" viewBox="0 0 6 9"><path d="M1 1 L5 4.5 L1 8" fill="none" stroke="#555" stroke-width="1.5"/></svg></span>
  </div>
  <div class="quote-box">
    <svg class="quote-mark" width="32" height="28" viewBox="0 0 32 28"><path d="M2 28 L2 12 Q2 2 12 0 L12 6 Q7 8 7 12 L13 12 L13 28 Z M18 28 L18 12 Q18 2 28 0 L28 6 Q23 8 23 12 L29 12 L29 28 Z" fill="#aaa"/></svg>
    <div class="quote-head">Lorem Ipsum is simply</div>
    <div class="quote-sub">Dolor Sit Amet</div>
    <p>Lorem Ipsum is simply dummy text of the priing and typesetting industry. Lorem Ipsum has been the industry's stdard dummy text ever<br><br>when an unknown printer took a galley of type and scrambled it to make a type spemen book.</p>
  </div>
</aside>

<section class="projects">
  <h2 class="section-title">Latest Projects</h2>
  <article class="card" style="left:79px">
    <div class="card-photo" role="img" aria-label="Photo of a call-centre agent with a headset and colleagues"></div>
    <div class="card-title">Company News</div>
    <p>Lorem Ipsum is simply dummy text of the printing dummy text ever since the 1500s Lorem Ipsum Lorem Ipsum is simply...</p>
  </article>
  <article class="card" style="left:396px">
    <div class="card-photo" role="img" aria-label="Photo of a businessman holding a silver puzzle piece" style="background:linear-gradient(90deg,#e9e9e9,#b8b8bd 50%,#7c7f86)"></div>
    <div class="card-title">Services</div>
    <p>Lorem Ipsum is simply dummy text of the printing dummy text ever since the 1500s Lorem Ipsum Lorem Ipsum is simply...</p>
  </article>
  <article class="card" style="left:711px">
    <div class="card-photo" role="img" aria-label="Photo of two business partners in an office" style="background:linear-gradient(90deg,#e6e9ea,#8a8a8a 45%,#2a2a2e 75%,#ece8e4)"></div>
    <div class="card-title">Support</div>
    <p>Lorem Ipsum is simply dummy text of the printing dummy text ever since the 1500s Lorem Ipsum Lorem Ipsum is simply...</p>
  </article>
</section>

<footer class="site-footer">©&nbsp; 2012. ALL RIGHTS RESERVED.</footer>

</body>
</html>
```